Modern web-site for a game changer new health app!

We need a very clean UX / UI design for our company website that will be used to sell our brand to large corporations and their employees. If we find a good match, we'd need you to do the app design and some graphics for ongoing design needs.

For a first of its kind app developed at Brockwell University, making licensed holistic medicine accessible to everyday people through access and curation by democratizing holistic health.

Please read the details attached thoroughly and reach out if you have any questions. Many thanks!
Updates

I've updated our requirements to make it easier, please review new details in the PDF shared. Many thanks!

Final brief refinement just uploaded, much has been simplified with very clear guidelines, please update and apply. thanks much!

Target Market(s)

corporate employees and large C level corporate leaders

Industry/Entity Type

wellness

Number of Pages Required

4 page

Font styles to use
Other font styles liked:
• We need website design now and app and socials after, hoping the designer we choose now can work with us on a regular basis going forward

Requirements
Must have
• clean, modern, minimal rich
Nice to have
• some added touches to give a custom feel
Should not have
• pictures, natural looking images or shapes

```html
<!DOCTYPE html>
<html lang="en">
<head>
<meta charset="utf-8">
<title>Aruvi – Wellness for Everyone</title>
<link href="https://fonts.googleapis.com/css2?family=Montserrat:wght@400;500;600;700;800&family=Roboto:ital,wght@0,400;0,500;0,700;1,400&display=swap" rel="stylesheet">
<style>
:root{
  --orange:#e8700f;
  --brown:#7a2a0c;
  --beige:#e3cfbb;
  --cream:#f2e2c6;
  --ink:#222;
  --grey:#666;
  --footer:#232323;
}
*{box-sizing:border-box;margin:0;padding:0}
html,body{width:1200px;height:5093px;overflow:hidden;background:#fff}
body{position:relative;font-family:"Roboto",sans-serif;color:var(--ink)}
.abs{position:absolute}
.center{text-align:center}
h1,h2,h3{font-family:"Montserrat",sans-serif;font-weight:800}
.accent{color:var(--orange)}
.btn{position:absolute;display:flex;align-items:center;justify-content:center;border-radius:40px;color:#fff;font-weight:700;text-transform:uppercase;background:linear-gradient(90deg,#e35a0c,#f07a14);box-shadow:0 4px 10px rgba(200,80,10,.35)}
.nav{top:0;left:0;width:1200px;height:115px;background:#fff}
.logo{font-family:"Montserrat",sans-serif;font-weight:800;color:var(--orange);font-size:72px;letter-spacing:1px}
.nav a{position:absolute;top:48px;font-size:14px;font-weight:500;color:var(--ink);text-decoration:none;text-transform:uppercase}
.hero{top:115px;left:0;width:1200px;height:617px;background:radial-gradient(ellipse at 20% 40%,#9fb09a 0%,#3d5a2e 35%,#1f3318 70%,#2b4a1d 100%)}
.hero h1{position:absolute;top:155px;left:0;width:1200px;text-align:center;color:#fff;font-size:46px}
.hero .tag{position:absolute;top:226px;width:1200px;text-align:center;color:#fff;font-size:27px}
.hero .sub{position:absolute;top:282px;width:1200px;text-align:center;color:#fff;font-size:17px}
.how{top:619px;left:144px;width:912px;height:449px;background:var(--beige);border-radius:70px 0 70px 0}
.how h2{position:absolute;top:46px;width:100%;text-align:center;color:var(--brown);font-size:37px}
.step-t{position:absolute;font-size:14px;font-weight:500;text-transform:uppercase;text-align:center;width:260px}
.step-d{position:absolute;font-size:12.5px;color:#6a5a50;text-align:center;width:240px;line-height:20px}
.card-img{position:absolute;top:1368px;width:286px;height:214px;border-radius:0 0 60px 0}
.card-label{position:absolute;top:1608px;width:286px;text-align:center;font-size:18px;font-weight:500;line-height:29px}
.arrow-btn{position:absolute;width:44px;height:44px;border:1.5px solid #555;border-radius:50%;display:flex;align-items:center;justify-content:center}
.clients{top:1754px;left:0;width:1200px;height:605px;background:linear-gradient(180deg,#e06e12 0%,#b3380a 50%,#98160a 100%);border-radius:110px 0 110px 0}
.client-ico{position:absolute;top:209px;width:154px;height:154px;border-radius:50%;background:radial-gradient(circle,#a81a0c,#7c0f06)}
.client-lbl{position:absolute;top:378px;width:220px;text-align:center;color:#fff;font-size:18px;font-weight:500}
.trusted{position:absolute;top:454px;left:326px;width:550px;height:62px;border-radius:32px;background:rgba(255,255,255,.12);display:flex;align-items:center;justify-content:center;gap:26px;color:#fff}
.para{font-size:16px;color:var(--grey);line-height:34px}
.care{top:2971px;left:190px;width:1010px;height:413px;background:var(--cream)}
.stat{position:absolute;top:3614px;width:186px;height:186px;border-radius:50%;border:5px solid #f0aa6a;display:flex;flex-direction:column;align-items:center;justify-content:center;background:#fff}
.stat b{font-size:40px;color:var(--orange);font-weight:700}
.stat span{font-size:13px;text-align:center;line-height:16px}
.contact{top:3940px;left:0;width:1200px;height:805px;background:linear-gradient(180deg,#ee8412 0%,#e04f0c 55%,#c21c0c 100%);border-radius:110px 0 110px 0}
.field{position:absolute;background:#fff;border-radius:6px;font-size:13px;color:#444;padding:16px 30px}
.testi{top:3835px;left:144px;width:912px;height:194px;background:#fff;border-radius:0 0 26px 26px}
.footer{top:4745px;left:0;width:1200px;height:348px;background:var(--footer)}
</style>
</head>
<body>

<header class="abs nav">
  <div class="abs logo" style="left:146px;top:10px">Aruvi</div>
  <a style="left:525px;color:var(--orange)">Complementary</a>
  <a style="left:690px">Enterprise</a>
  <a style="left:815px">Members</a>
  <div class="btn" style="left:918px;top:36px;width:138px;height:42px;font-size:13px">Get Started</div>
</header>

<section class="abs hero" role="img" aria-label="Close-up photo of white flower blossoms among green leaves">
  <h1>WELLNESS <span class="accent">FOR EVERYONE</span></h1>
  <p class="tag">Modern Science meets Ancient Wisdom</p>
  <p class="sub">Get 1 on 1 PHD care on US for personalized remedies</p>
  <div class="btn" style="left:496px;top:343px;width:208px;height:58px;font-size:16px">Get Started</div>
</section>

<section class="abs how">
  <h2>HOW IT WORKS</h2>
  <svg class="abs" style="left:0;top:0" width="912" height="449" viewBox="0 0 912 449">
    <defs>
      <marker id="ah" markerWidth="10" markerHeight="10" refX="6" refY="5" orient="auto"><path d="M0,0 L8,5 L0,10" fill="none" stroke="currentColor" stroke-width="2"/></marker>
    </defs>
    <path d="M84,256 Q120,200 158,208" stroke="#1f2b22" stroke-width="4" fill="none"/>
    <path d="M258,206 Q300,200 336,250" stroke="#1f2b22" color="#1f2b22" stroke-width="4" fill="none" marker-end="url(#ah)"/>
    <path d="M350,300 L395,308" stroke="#e08a1a" stroke-width="4" fill="none"/>
    <path d="M506,300 Q560,290 590,232" stroke="#e08a1a" color="#e08a1a" stroke-width="4" fill="none" marker-end="url(#ah)"/>
    <path d="M748,208 Q790,204 824,250" stroke="#9a3a0e" color="#9a3a0e" stroke-width="4" fill="none" marker-end="url(#ah)"/>
    <path d="M148,203 A60,60 0 0 0 268,203" fill="#1f2b22"/>
    <circle cx="208" cy="203" r="42" fill="#fff"/>
    <path d="M391,308 A60,60 0 0 1 511,308" fill="#e08a1a"/>
    <circle cx="451" cy="308" r="42" fill="#fff"/>
    <path d="M640,203 A60,60 0 0 0 760,203" fill="#9a3a0e"/>
    <circle cx="700" cy="203" r="42" fill="#fff"/>
    <text x="208" y="213" text-anchor="middle" font-family="Montserrat,sans-serif" font-size="28" font-weight="500" fill="#222">01</text>
    <text x="451" y="318" text-anchor="middle" font-family="Montserrat,sans-serif" font-size="28" font-weight="500" fill="#e08a1a">02</text>
    <text x="700" y="213" text-anchor="middle" font-family="Montserrat,sans-serif" font-size="28" font-weight="500" fill="#7a2a0c">03</text>
  </svg>
  <div class="step-t" style="left:326px;top:136px">Get matched with a specialist</div>
  <div class="step-d" style="left:336px;top:168px">Sed ut perspiciatis unde omnis iste natus error sit voluptatem cusantium doloremque laudantium</div>
  <div class="step-t" style="left:70px;top:288px">Take test</div>
  <div class="step-d" style="left:80px;top:320px">Sed ut perspiciatis unde omnis iste natus error sit voluptatem cusantium doloremque laudantium</div>
  <div class="step-t" style="left:570px;top:288px">Video consult</div>
  <div class="step-d" style="left:580px;top:320px">Sed ut perspiciatis unde omnis iste natus error sit voluptatem cusantium doloremque laudantium</div>
</section>

<section class="health">
  <h2 class="abs center" style="top:1170px;width:1200px;font-size:37px;color:var(--brown)">HEALTH FOR <span class="accent">EVERYONE</span></h2>
  <p class="abs center" style="top:1240px;width:1200px;font-size:22px">All-Inclusive Holistic Wellness&nbsp; $25 / month</p>
  <p class="abs center" style="top:1280px;width:1200px;font-size:16px">Time tested science changing the lives of millions at a price everyone can afford.</p>
  <div class="arrow-btn" style="left:71px;top:1453px"><svg width="16" height="16"><path d="M10,2 L4,8 L10,14" stroke="#333" stroke-width="2" fill="none"/></svg></div>
  <div class="arrow-btn" style="left:1083px;top:1453px"><svg width="16" height="16"><path d="M6,2 L12,8 L6,14" stroke="#333" stroke-width="2" fill="none"/></svg></div>
  <div class="card-img" role="img" aria-label="Photo of a smiling scientist examining plants" style="left:144px;background:linear-gradient(135deg,#dfe4dc,#9aa89a)"></div>
  <div class="card-img" role="img" aria-label="Photo of gloved hands handling supplement capsules" style="left:457px;background:linear-gradient(135deg,#7ea6d8,#cfd6d8);border-bottom:4px solid var(--orange)"></div>
  <div class="card-img" role="img" aria-label="Photo of lab test tubes in an orange rack" style="left:771px;background:linear-gradient(135deg,#e46a12,#2b4fa0)"></div>
  <div class="card-label" style="left:144px">1 on 1 with Holistic<br>Doctors &amp; Unlimited Texting</div>
  <div class="card-label" style="left:457px">Personalized<br>Custom Supplements</div>
  <div class="card-label" style="left:771px">Gut, Hormone &amp; Cellular<br>Lab Tests</div>
</section>

<section class="abs clients">
  <h2 class="abs center" style="top:80px;width:1200px;color:#fff;font-size:36px">OUR CLIENTS</h2>
  <p class="abs center" style="top:145px;width:1200px;color:#fff;font-size:18px;font-family:Montserrat,sans-serif">Trust Us to Provide Holistic Health for Their Team, So Should You!</p>
  <div class="client-ico" role="img" aria-label="Line icon for any challenge" style="left:261px"></div>
  <div class="client-ico" role="img" aria-label="Clock icon for any time" style="left:522px;border:3px solid #fff"></div>
  <div class="client-ico" role="img" aria-label="Globe icon for anywhere" style="left:783px"></div>
  <div class="client-lbl" style="left:228px">Any Challenge</div>
  <div class="client-lbl" style="left:489px">Any Time</div>
  <div class="client-lbl" style="left:750px">Anywhere</div>
  <div class="trusted"><span style="font-size:17px">Trusted by:</span><span style="font-size:34px;font-weight:500">Northfield Apparel</span></div>
</section>

<section class="ent">
  <h2 class="abs" style="left:144px;top:2458px;color:var(--brown);font-size:37px">ARUVI FOR <span class="accent">ENTERPRISE</span></h2>
  <p class="abs" style="left:144px;top:2522px;font-size:23px;line-height:29px">We're all feeling a strain on our<br>health these days</p>
  <p class="abs para" style="left:144px;top:2597px;width:470px">Leaders of industry aren't accidental, they know employee retention &amp; experience work in their favor.<br>&nbsp;In these tumultuous times, Solace brings much-needed relief and benefits to teams that bring their all in return.</p>
  <div class="btn" style="left:144px;top:2768px;width:275px;height:56px;font-size:16px">Aruvi for Enterprise</div>
  <div class="abs" style="left:660px;top:2450px;width:392px;height:392px;border-radius:50%;border:7px solid var(--orange)"></div>
  <div class="abs" role="img" aria-label="Photo of a doctor reviewing a clipboard with a senior patient" style="left:664px;top:2454px;width:372px;height:372px;border-radius:50%;background:linear-gradient(135deg,#b9c3cc,#5d5a5c)"></div>
</section>

<section class="abs care"></section>
<div class="abs" style="left:143px;top:2972px;width:410px;height:410px;border-radius:50%;background:var(--cream)"></div>
<div class="abs" role="img" aria-label="Photo of a smiling woman shaking hands with a doctor" style="left:174px;top:3003px;width:348px;height:348px;border-radius:50%;background:linear-gradient(135deg,#dde6ec,#3a3c46)"></div>
<h2 class="abs" style="left:562px;top:3066px;font-size:39px;line-height:46px;color:var(--brown)">HUMAN CARE POWERED<br><span class="accent">BY TECHNOLOGY</span></h2>
<p class="abs" style="left:563px;top:3174px;font-size:23px">All Your Mind Body Needs Met In One Place</p>
<p class="abs para" style="left:563px;top:3218px;width:380px">All practitioners work collaboratively to provide the best care.</p>

<h3 class="abs" style="left:150px;top:3498px;font-size:28px;font-weight:700;line-height:39px">Clinically proven to help people<br>not only feel better, but thrive.</h3>
<h3 class="abs" style="left:720px;top:3498px;font-size:28px;font-weight:700;line-height:39px">Members love the easy<br>&amp; effective experience.</h3>
<div class="stat" style="left:150px"><b>80%</b><span style="font-size:24px;font-weight:500;line-height:28px">Aruvi</span></div>
<div class="stat" style="left:362px"><b>20%</b><span>Leading corporate<br>health programs</span></div>
<div class="stat" style="left:722px"><b style="display:flex;align-items:center;gap:8px">5<svg width="44" height="42" viewBox="0 0 24 23"><path d="M12,0 L15,8 L24,8.5 L17,14 L19.5,23 L12,18 L4.5,23 L7,14 L0,8.5 L9,8 Z" fill="#e8700f"/></svg></b><span>average rating after<br>every care session</span></div>

<section class="abs contact">
  <h2 class="abs center" style="top:172px;width:1200px;color:#fff;font-size:37px">WE'D LOVE TO HEAR FROM YOU</h2>
  <p class="abs center" style="top:240px;width:1200px;color:#fff;font-size:16px;line-height:28px">Tell us a little about you and your company to see if you qualify for our<br>membership-based model at no cost to your company.</p>
  <p class="abs center" style="top:311px;width:1200px;color:#fff;font-size:20px;font-family:Montserrat,sans-serif"><svg width="20" height="15" style="vertical-align:-1px;margin-right:10px"><rect width="20" height="15" rx="2" fill="#fff"/><path d="M1,1 L10,8 L19,1" stroke="#e0530c" stroke-width="2" fill="none"/></svg>info@solaceforhealth.net</p>
  <div class="field" style="left:279px;top:382px;width:314px;height:47px">Name</div>
  <div class="field" style="left:607px;top:382px;width:314px;height:47px">Email</div>
  <div class="field" style="left:279px;top:443px;width:314px;height:48px">How many people in your location?</div>
  <div class="field" style="left:607px;top:443px;width:314px;height:48px">How many locations?</div>
  <div class="field" style="left:279px;top:504px;width:642px;height:113px">Anything else we can help you with?</div>
  <div class="btn" style="left:463px;top:653px;width:276px;height:63px;font-size:17px;border:2px solid #fff">Submit Message</div>
</section>

<section class="abs testi">
  <div class="abs center" style="top:18px;width:912px;font-size:46px;color:var(--orange);font-family:Georgia,serif;font-style:italic">“</div>
  <p class="abs center" style="top:52px;left:90px;width:732px;font-size:14.5px;font-style:italic;line-height:26px">"I'm so glad that I chose Solace for our company. Who knew that something that I could just expense from petty cash would transform the lives of so many people here including myself."</p>
  <p class="abs center" style="top:122px;width:912px;font-size:13px;color:var(--orange)">DANA | FIELD OPERATIONS,April 11, 2016</p>
  <div class="arrow-btn" style="left:39px;top:65px;width:24px;height:24px;border-color:#aaa"><svg width="10" height="10"><path d="M7,1 L3,5 L7,9" stroke="#777" stroke-width="1.5" fill="none"/></svg></div>
  <div class="arrow-btn" style="left:849px;top:65px;width:24px;height:24px;border-color:#aaa"><svg width="10" height="10"><path d="M3,1 L7,5 L3,9" stroke="#777" stroke-width="1.5" fill="none"/></svg></div>
</section>

<footer class="abs footer">
  <div class="abs logo" style="left:154px;top:70px;font-size:82px">Aruvi</div>
  <div class="abs" style="left:461px;top:45px;width:1px;height:150px;background:#555"></div>
  <p class="abs" style="left:508px;top:63px;color:#fff;font-size:17px;font-weight:500">SUBSCRIBE TO OUR NEWSLETTER</p>
  <div class="abs" style="left:508px;top:116px;width:370px;height:46px;border:1.5px solid #aaa;border-radius:24px;color:#ddd;font-size:13px;padding:14px 44px">Enter Email</div>
  <div class="btn" style="left:892px;top:116px;width:156px;height:46px;font-size:14px;border:2px solid #fff">Subscribe</div>
  <p class="abs center" style="top:288px;width:1200px;color:#fff;font-size:14px">© 2025 Aruvi.All rights reserved&nbsp; |&nbsp; Privacy Policy&nbsp; |&nbsp; Terms of Use</p>
</footer>

</body>
</html>
```